Road Construction Company needs business cards

We would like a new business card designed for our business.

We're a road construction company based in Qld, Australia.

Can the business card please have the following information on it.

Name: Warren Halbeck
Position: General Manager
Phone: 0472 915 348
Email: Warren.halbeck@tovrin.com.au
Address: 87 Marrow Ave, Pendlebay, QLD, 4023
Website: www.tovrin.com.au

Visually we'd like the card to be professional and simple.

Attached is our logo.

Our website is www.tovrin.com.au

Target Market(s)

Men aged 25-60

Contact Information for Business Card

As listed in project description

Font styles to use
Serif

Requirements
Must have
• Large logo on back of card

```html
<!DOCTYPE html>
<html lang="en">
<head>
<meta charset="utf-8">
<title>Tovrin Business Card</title>
<link rel="stylesheet" href="https://fonts.googleapis.com/css2?family=Montserrat:wght@700;800&family=Mulish:wght@400&display=swap">
<style>
  :root {
    --stage: #9b9b9b;
    --navy: #0d4a9b;
    --royal: #0b55a6;
    --deep: #1b3f86;
    --light-blue: #2fa7dc;
    --ink: #444444;
    --white: #ffffff;
  }
  * { margin: 0; padding: 0; box-sizing: border-box; }
  html, body { width: 1200px; height: 588px; overflow: hidden; }
  body { background: var(--stage); position: relative; font-family: "Mulish", sans-serif; }

  .card { position: absolute; top: 143px; width: 487px; height: 287px; overflow: hidden; }

  /* Back of card */
  .card-back { left: 87px; background: var(--royal); }
  .back-texture {
    position: absolute; inset: 0;
    background: linear-gradient(115deg, var(--deep) 0%, var(--royal) 45%, #2c6cc0 100%);
  }
  .back-logo {
    position: absolute; right: 20px; top: 196px;
    font-family: "Montserrat", sans-serif; font-weight: 800;
    font-size: 38px; letter-spacing: 1px; line-height: 1;
    color: var(--white);
  }

  /* Front of card */
  .card-front { left: 622px; background: var(--white); }
  .front-logo {
    position: absolute; right: 22px; top: 26px;
    font-family: "Montserrat", sans-serif; font-weight: 800;
    font-size: 36px; letter-spacing: 1px; line-height: 1;
    color: var(--navy);
  }
  .name-marker { position: absolute; left: 0; top: 139px; width: 11px; height: 34px; background: var(--light-blue); }
  .person-name {
    position: absolute; left: 23px; top: 138px;
    font-family: "Montserrat", sans-serif; font-weight: 800;
    font-size: 19px; color: var(--navy); line-height: 1; letter-spacing: 0.2px;
  }
  .person-role { position: absolute; left: 23px; top: 160px; font-size: 13px; color: var(--ink); }

  .contact-list { position: absolute; left: 23px; top: 207px; list-style: none; }
  .contact-list li { display: flex; align-items: center; height: 19px; font-size: 13px; color: var(--ink); }
  .contact-list svg { width: 11px; height: 11px; margin-right: 5px; flex: none; }

  .address { position: absolute; right: 22px; top: 226px; text-align: right; font-size: 13px; line-height: 19px; color: var(--ink); }
  .corner-bar { position: absolute; left: 346px; bottom: 0; width: 119px; height: 11px; background: var(--light-blue); }
</style>
</head>
<body>
  <section class="card card-back">
    <div class="back-texture" role="img" aria-label="Repeating pattern of brand chevrons in shades of blue"></div>
    <div class="back-logo">TOVRIN</div>
  </section>

  <section class="card card-front">
    <div class="front-logo">TOVRIN</div>

    <div class="name-marker"></div>
    <h1 class="person-name">WARREN HALBECK</h1>
    <p class="person-role">General Manager</p>

    <ul class="contact-list">
      <li>
        <svg viewBox="0 0 24 24" aria-hidden="true"><path fill="#2fa7dc" d="M6.6 10.8a15.1 15.1 0 0 0 6.6 6.6l2.2-2.2c.3-.3.7-.4 1-.2 1.1.4 2.3.6 3.6.6.6 0 1 .4 1 1V20c0 .6-.4 1-1 1A17 17 0 0 1 3 4c0-.6.4-1 1-1h3.5c.6 0 1 .4 1 1 0 1.3.2 2.5.6 3.6.1.3 0 .7-.2 1z"/></svg>
        0472 915 348
      </li>
      <li>
        <svg viewBox="0 0 24 24" aria-hidden="true"><path fill="#2fa7dc" d="M2 5h20v14H2z"/><path fill="none" stroke="#fff" stroke-width="2" d="M3 6l9 7 9-7"/></svg>
        Warren.halbeck@tovrin.com.au
      </li>
      <li>
        <svg viewBox="0 0 24 24" aria-hidden="true"><circle cx="12" cy="12" r="10" fill="#2fa7dc"/><path fill="none" stroke="#fff" stroke-width="1.5" d="M2 12h20M12 2c3 3 3 17 0 20M12 2c-3 3-3 17 0 20"/></svg>
        www.tovrin.com.au
      </li>
    </ul>

    <address class="address" style="font-style: normal;">87 Marrow Ave<br>Pendlebay, QLD, 4023</address>
    <div class="corner-bar"></div>
  </section>
</body>
</html>
```